Brightmill Data Works

Our company is about IT hardwares and IT solutions. IT hardware such as PC, RAMS, storage and servers. IT solutions such as project management, BA. We are also selling new technology too.

Target Market(s)

Consumer, Small to Medium Business, Corporate

Requirements
Must have
• The business card must have the following:
• Name:
• Title:
• Contact Number:
• Email address:
• Website:
• Color: Must match the logo color upgrade

```html
<!DOCTYPE html>
<html lang="en">
<head>
<meta charset="utf-8">
<title>Brightmill Data Works — Business Card</title>
<link rel="stylesheet" href="https://fonts.googleapis.com/css2?family=Oswald:wght@500&family=Work+Sans:wght@400;600&display=swap">
<style>
  :root {
    --backdrop: #1c1c1c;
    --card: #141414;
    --card-edge: #242424;
    --emboss: #6e6e6e;
    --emboss-title: #7a7a7a;
    --foil: #d4d4d4;
    --foil-dim: #a8a8a8;
    --rule: #4a4a4a;
  }
  * { margin: 0; padding: 0; box-sizing: border-box; }
  html, body {
    width: 1200px; height: 900px; overflow: hidden;
    background: radial-gradient(ellipse at 60% 40%, #262626 0%, var(--backdrop) 70%);
    font-family: "Work Sans", sans-serif;
  }
  .canvas { position: relative; width: 1200px; height: 900px; }
  .card {
    position: absolute; left: 250px; width: 700px; height: 400px;
    background: linear-gradient(135deg, var(--card) 0%, #1d1d1d 60%, var(--card) 100%);
    border: 1px solid var(--card-edge);
    box-shadow: 0 18px 40px rgba(0,0,0,0.6);
  }
  .card--front { top: 40px; }
  .card--back { top: 470px; }

  .brand {
    position: absolute; inset: 0;
    display: flex; align-items: center; justify-content: center; gap: 16px;
  }
  .brand__mark { width: 26px; height: 26px; background: var(--foil); }
  .brand__name {
    font-weight: 600; font-size: 40px; letter-spacing: 1px;
    color: var(--foil); text-transform: uppercase;
  }

  .person {
    position: absolute; left: 40px; top: 128px; width: 255px; text-align: right;
  }
  .person__name {
    font-family: "Oswald", sans-serif; font-weight: 500; font-size: 40px;
    letter-spacing: 0.5px; color: var(--emboss);
    text-shadow: 1px 1px 0 rgba(0,0,0,0.7);
    text-transform: uppercase; line-height: 1.1;
  }
  .person__title {
    font-size: 18px; color: var(--emboss-title);
    letter-spacing: 1px; margin-top: 2px;
  }
  .divider {
    position: absolute; left: 325px; top: 120px; width: 1px; height: 100px;
    background: var(--rule);
  }
  .contact { position: absolute; left: 350px; top: 128px; list-style: none; }
  .contact__item {
    display: flex; align-items: center; gap: 12px;
    font-size: 20px; color: var(--foil); letter-spacing: 0.5px;
    margin-bottom: 6px;
  }
  .contact__item svg { width: 14px; height: 14px; flex: none; }
  .address {
    position: absolute; left: 60px; bottom: 48px;
    font-size: 19px; color: var(--foil-dim); letter-spacing: 0.5px;
  }
</style>
</head>
<body>
<main class="canvas">
  <section class="card card--front">
    <div class="brand">
      <span class="brand__mark"></span>
      <span class="brand__name">Brightmill Data Works</span>
    </div>
  </section>

  <section class="card card--back">
    <div class="person">
      <p class="person__name">Daniel Reyes</p>
      <p class="person__title">Director</p>
    </div>
    <div class="divider"></div>
    <ul class="contact">
      <li class="contact__item">
        <svg viewBox="0 0 14 14" aria-hidden="true"><path d="M3 1 L5 1 L6 4 L4.5 5 Q6 8.5 9 9.5 L10 8 L13 9 L13 11 Q12 13 10 13 Q2 11 1 3 Q1 1 3 1 Z" fill="none" stroke="#d4d4d4" stroke-width="1.2"/></svg>
        615-555-0142
      </li>
      <li class="contact__item">
        <svg viewBox="0 0 14 14" aria-hidden="true"><rect x="1" y="3" width="12" height="8" fill="none" stroke="#d4d4d4" stroke-width="1.2"/><path d="M1 3 L7 8 L13 3" fill="none" stroke="#d4d4d4" stroke-width="1.2"/></svg>
        info@brightmilldata.com
      </li>
      <li class="contact__item">
        <svg viewBox="0 0 14 14" aria-hidden="true"><circle cx="7" cy="7" r="5.5" fill="none" stroke="#d4d4d4" stroke-width="1.1"/><ellipse cx="7" cy="7" rx="2.5" ry="5.5" fill="none" stroke="#d4d4d4" stroke-width="1"/><path d="M1.5 7 H12.5" stroke="#d4d4d4" stroke-width="1"/></svg>
        www.brightmilldata.com
      </li>
    </ul>
    <p class="address">2750 Orchard Valley Rd Rosa, CA 95410-3018</p>
  </section>
</main>
</body>
</html>
```